web page design with coding

We are a start up insurance agency who needs to design a full functional web page. we recently did a postcard design though drawkettle I will upload the final project for you to see the color scheme/font we would like to continue to use. I also have a rough draft of verbage I would like our website to have. I will upload that as well.

Reason: I am sorry but the person who will make the final decision on the website is out of the country at the moment and will make the final decision when he returns.

Industry/Entity Type

Insurance

Coding

Coded - Design and coding required

```html
<!DOCTYPE html>
<html lang="en">
<head>
<meta charset="utf-8">
<title>Meridian Shield Insurance Group</title>
<link rel="stylesheet" href="https://fonts.googleapis.com/css2?family=Open+Sans:wght@400;600;700&display=swap">
<style>
:root{
  --blue:#1b8dcc;
  --blue-dark:#0f6fa6;
  --navy:#27314d;
  --ink:#333;
  --muted:#666;
  --line:#cfd4d8;
  --footer-dark:#111;
  --white:#fff;
}
*{box-sizing:border-box;margin:0;padding:0}
html,body{width:1200px;height:3396px;overflow:hidden}
body{position:relative;font-family:"Open Sans",Arial,sans-serif;color:var(--ink);background:var(--white)}
.abs{position:absolute}

/* header */
.topbar{left:0;top:0;width:1200px;height:57px;background:var(--blue)}
.topbar .phone{left:310px;top:18px;color:var(--white);font-size:13px;font-weight:600;display:flex;align-items:center;gap:8px}
.social{display:flex;gap:10px;right:96px;top:10px}
.social span{width:34px;height:34px;border-radius:50%;background:var(--white);display:block}
.brand{left:109px;top:11px;width:180px;height:107px;background:var(--white);border:3px solid #ddd;box-shadow:0 2px 6px rgba(0,0,0,.25);display:flex;flex-direction:column;align-items:center;justify-content:center}
.brand b{font-size:40px;font-weight:700;color:var(--navy);line-height:1}
.brand small{font-size:10px;color:var(--navy);margin-top:6px}
.nav{left:0;top:57px;width:1200px;height:83px;border-bottom:1px solid #e3e3e3}
.nav ul{list-style:none;position:absolute;left:534px;top:33px;display:flex;gap:0}
.nav li{font-size:12px;font-weight:600;color:#333;margin-right:68px;position:relative}
.nav li:last-child{margin-right:0}
.nav li.active{color:var(--blue)}
.nav li.active::after{content:"";position:absolute;left:-12px;right:-12px;top:43px;height:4px;background:var(--blue)}

/* hero */
.hero{left:0;top:140px;width:1200px;height:442px;background:linear-gradient(90deg,#2a2a26 0%,#3b3a33 40%,#6a6e5a 65%,#4f6a3c 100%)}
.hero h1{position:absolute;left:108px;top:182px;color:var(--white);font-size:31px;font-weight:400;letter-spacing:.5px}
.hero p{position:absolute;left:108px;top:230px;width:440px;color:#ddd;font-size:11.5px;line-height:23px}
.hero .arrows{position:absolute;left:108px;top:292px;color:var(--white);font-size:20px;font-weight:700;letter-spacing:6px}

/* section headings */
.h2{font-size:26px;font-weight:400;color:#222;display:flex;align-items:center;gap:10px;text-transform:uppercase}
.center{left:0;width:1200px;justify-content:center;text-align:center}
.divider{left:110px;width:980px;height:14px;background:radial-gradient(ellipse at center top,rgba(0,0,0,.35) 0%,rgba(0,0,0,0) 70%)}
.body-text{font-size:11.5px;line-height:30px;color:var(--muted)}

.welcome-text{left:113px;top:693px;width:976px;text-align:center}

/* about */
.about-text{left:111px;top:984px;width:650px}
.agents{left:788px;top:930px;width:301px;height:234px;background:var(--blue);color:var(--white)}
.agents h3{position:absolute;left:22px;top:22px;font-size:19px;font-weight:400;display:flex;gap:8px;align-items:center}
.agents .nav-arrows{position:absolute;right:28px;top:20px;font-size:20px;font-weight:700;letter-spacing:10px}
.agents .sep{position:absolute;left:22px;right:22px;top:60px;height:1px;background:rgba(255,255,255,.4)}
.agents .avatar{position:absolute;left:24px;top:75px;width:44px;height:44px;border-radius:50%;background:linear-gradient(#7d8fa3,#3d4c5f)}
.agents .name{position:absolute;left:80px;top:80px;font-size:13px;line-height:18px}
.agents .name small{display:block;font-size:11px}
.agents p{position:absolute;left:24px;top:128px;width:250px;font-size:11.5px;line-height:26px}

/* mission */
.mission{left:0;top:1213px;width:1200px;height:327px;background:linear-gradient(180deg,#1f2844 0%,#2f3a5c 60%,#39456a 100%)}
.mission .h2{position:absolute;top:102px;color:var(--white)}
.mission p{position:absolute;left:126px;top:150px;width:948px;text-align:center;color:#e6e8ee;font-size:15px;line-height:34px}

/* services */
.card{width:475px}
.card .photo{position:absolute;left:0;top:0;width:475px;height:246px;box-shadow:0 2px 6px rgba(0,0,0,.3)}
.card .label{position:absolute;left:98px;top:192px;width:312px;height:54px;background:var(--blue);color:var(--white);font-size:19px;display:flex;align-items:center;justify-content:center;text-transform:uppercase}
.card p{position:absolute;left:0;top:258px;width:475px;text-align:center}
.card .more{position:absolute;left:0;top:418px;width:475px;text-align:center;font-size:12px;color:var(--blue);text-transform:uppercase}
.card-business{left:113px;top:1592px}
.card-business .photo{background:linear-gradient(135deg,#d9dbd6,#a69a86 50%,#e8e6e0)}
.card-personal{left:614px;top:1592px}
.card-personal .photo{background:linear-gradient(135deg,#e9ecef,#b9bfc8 50%,#dfe6ec)}

/* form */
.contact-intro{left:150px;top:2180px;width:900px;text-align:center}
.field{height:55px;border:1px solid var(--line);border-radius:2px;background:var(--white);font-size:11px;color:#777;padding:0 20px;display:flex;align-items:center}
.col-l{left:113px;width:473px}
.col-r{left:614px;width:475px}
.comments{left:113px;top:2538px;width:976px;height:140px;align-items:flex-start;padding-top:22px}
.attach{top:2712px;background:#ececec}
.browse{left:614px;top:2712px;width:165px;height:55px;background:#f3f3f3;border:1px solid #ddd;font-size:11px;display:flex;align-items:center;justify-content:center;color:#444}
.submit{left:514px;top:2805px;width:172px;height:59px;background:var(--blue-dark);color:var(--white);font-size:17px;display:flex;align-items:center;justify-content:center;border-radius:2px;box-shadow:0 2px 3px rgba(0,0,0,.3)}

/* map */
.map{left:0;top:2923px;width:1200px;height:176px;background:linear-gradient(180deg,#e8e6df,#dcdcd2)}
.map-pin{left:600px;top:2989px}
.map-tag{left:648px;top:3002px;background:#333;color:var(--white);font-size:11px;padding:3px 9px}

/* footer */
.footer{left:0;top:3099px;width:1200px;height:220px;background:var(--blue);color:var(--white)}
.footer h4{font-size:15px;font-weight:400;text-transform:uppercase;letter-spacing:.5px}
.footer .col{position:absolute;top:40px}
.footer ul{list-style:none;margin-top:16px}
.footer li{font-size:11px;line-height:24px}
.footer li::before{content:"\25B8 ";}
.blog-item{display:flex;gap:10px;margin-top:16px}
.blog-item .thumb{width:48px;height:42px;background:linear-gradient(#9aa8b6,#5d6b7a);flex:none}
.blog-item p{font-size:11px;line-height:21px;width:240px}
.contact-list p{font-size:11px;line-height:27px}
.news-note{font-size:11px;line-height:21px;width:200px;margin-top:12px}
.news-form{display:flex;margin-top:10px}
.news-form span{width:143px;height:30px;background:var(--white);color:#666;font-size:10px;display:flex;align-items:center;padding-left:10px}
.news-form b{width:55px;height:30px;background:var(--navy);font-size:10px;font-weight:400;display:flex;align-items:center;justify-content:center}
.footer .rings{display:flex;gap:12px;margin-top:14px}
.footer .rings span{width:34px;height:34px;border:2px solid var(--white);border-radius:50%;display:block}
.copyright{left:0;top:3319px;width:1200px;height:77px;background:var(--footer-dark);color:#ccc;font-size:11px;display:flex;align-items:center;justify-content:center}
</style>
</head>
<body>

<header>
  <div class="abs topbar">
    <div class="abs phone">
      <svg width="12" height="14" viewBox="0 0 12 14"><rect x="1" y="0" width="10" height="14" rx="2" fill="#fff"/><rect x="3" y="2" width="6" height="8" fill="#1b8dcc"/></svg>
      (555) 014-2270
    </div>
    <div class="abs social" aria-label="Social links"><span></span><span></span><span></span></div>
  </div>
  <nav class="abs nav">
    <ul>
      <li class="active">HOME</li><li>ABOUT US</li><li>SERVICES</li><li>PRODUCTS</li><li>NEWS</li><li>CONTACT US</li>
    </ul>
  </nav>
  <div class="abs brand"><b>MSIG</b><small>Meridian Shield Insurance Group</small></div>
</header>

<section class="abs hero" role="img" aria-label="Photo of a young family sitting together on a blanket in a park">
  <h1>MERIDIAN SHIELD INSURANCE GROUP</h1>
  <p>Meridian Shield Insurance Group has joined with regional &amp; national insurance companies to provide quality products and superior service.</p>
  <div class="arrows">«  »</div>
</section>

<h2 class="abs h2 center" style="top:638px">
  <svg width="26" height="22" viewBox="0 0 26 22"><path d="M0 10 Q0 0 10 0 V4 Q5 4 5 9 H10 V22 H0Z M14 10 Q14 0 24 0 V4 Q19 4 19 9 H24 V22 H14Z" fill="#1b8dcc"/></svg>
  Welcome to Meridian Shield Insurance Group
</h2>
<p class="abs body-text welcome-text">Meridian Shield Insurance Group has joined with regional &amp; national insurance companies to provide quality products and superior service. We take the time to discuss options and coverages, not to just sell insurance products. We strive to educate you in the decision making process to become an informed consumer. We specialize in commercial business &amp; personal insurance. We are committed to providing personal attention to all your insurance needs. At Meridian Shield Insurance Group, we are independent insurance agents. As independent agents, we do not work for any one insurance company; we sell coverage from several different companies. This allows us to focus on providing you with the right amount of insurance and the right type of coverage for your unique needs.</p>
<div class="abs divider" style="top:876px"></div>

<h2 class="abs h2" style="left:111px;top:934px">
  <svg width="22" height="24" viewBox="0 0 22 24"><circle cx="11" cy="6" r="6" fill="#1b8dcc"/><path d="M0 24 Q0 13 11 13 Q22 13 22 24Z" fill="#1b8dcc"/></svg>
  About Us
</h2>
<p class="abs body-text about-text">Established in 2015, Meridian Shield Insurance Group is a full service independent insurance agency. Our licensed agents have the experience to custom tailor a program to meet your specific needs &amp; our professional support staff will provide you with top notch customer service to help ease the burden of managing your insurance program. We have established relationships with carriers in order to offer you the most competitive products and services available in the marketplace today.<br>We look forward to working with you!</p>

<aside class="abs agents">
  <h3>
    <svg width="22" height="18" viewBox="0 0 22 18"><circle cx="6" cy="5" r="4" fill="#fff"/><circle cx="16" cy="5" r="4" fill="#fff"/><path d="M0 18 Q0 10 6 10 Q12 10 12 18Z M10 18 Q10 10 16 10 Q22 10 22 18Z" fill="#fff"/></svg>
    AGENTS
  </h3>
  <div class="nav-arrows">‹ ›</div>
  <div class="sep"></div>
  <div class="avatar" role="img" aria-label="Agent portrait"></div>
  <div class="name">Owen<small>Location</small></div>
  <p>Lorem ipsum dolor sit amet, consectetur adi piscing elit. Nulla gravida lacus mi, quis congue enim sodales eu.</p>
</aside>

<section class="abs mission" role="img" aria-label="Night city skyline in deep blue tones">
  <h2 class="h2 center">
    <svg width="26" height="22" viewBox="0 0 26 22"><circle cx="9" cy="12" r="7" fill="none" stroke="#fff" stroke-width="4"/><circle cx="20" cy="6" r="4" fill="none" stroke="#fff" stroke-width="3"/></svg>
    Our Mission
  </h2>
  <p>Meridian Shield Insurance Group is committed to providing the best risk management solutions to fit each client's unique needs. This includes providing creative solutions as if we were seeking insurance for our own family.</p>
</section>

<article class="abs card card-business">
  <div class="photo" role="img" aria-label="Photo of business people meeting around a table"></div>
  <div class="label">Business Insurance</div>
  <p class="body-text">Meridian Shield Insurance Group can help you take steps to protect your business and your family from the financial consequences of events that could disrupt operations, reduce profits, or even cause the business to go bankrupt. We know what questions to ask, what risks need to be identified, and most importantly, we understand how to best insure them.</p>
  <div class="more">▸ More details</div>
</article>
<article class="abs card card-personal">
  <div class="photo" role="img" aria-label="Photo of an agent reviewing documents with a client"></div>
  <div class="label">Personal Insurance</div>
  <p class="body-text">One size rarely fits all. Neither do standard personal insurance products. At Meridian Shield Insurance Group, we strive to understand your needs and provide tailored solutions. We present all viable options and equip you with the information you need to make informed decisions.</p>
  <div class="more">▸ More details</div>
</article>
<div class="abs divider" style="top:2066px"></div>

<h2 class="abs h2 center" style="top:2121px">
  <svg width="26" height="18" viewBox="0 0 26 18"><rect width="26" height="18" rx="2" fill="#1b8dcc"/><path d="M1 1 L13 10 L25 1" fill="none" stroke="#fff" stroke-width="2"/></svg>
  Contact &amp; Fill Submission Form
</h2>
<p class="abs body-text contact-intro">Vivamus sodales in augue a tristique. Sed hendrerit aliquet est, non cursus augue fringilla vitae. In eu ullamcorper nulla. Aenean est orci, accumsan et vestibulum et, accumsan quis justo. Nam in auctor metus, id commodo leo.</p>

<form>
  <div class="abs field col-l" style="top:2282px">Name</div>
  <div class="abs field col-r" style="top:2282px">Company</div>
  <div class="abs field col-l" style="top:2368px">Address</div>
  <div class="abs field col-r" style="top:2368px">Zip Code</div>
  <div class="abs field col-l" style="top:2454px">Phone</div>
  <div class="abs field col-r" style="top:2454px">Email Address</div>
  <div class="abs field comments">Comments &amp; Questions</div>
  <div class="abs field col-l attach">Attachments</div>
  <div class="abs browse">BROWSE</div>
  <div class="abs submit">SUBMIT</div>
</form>

<div class="abs map" role="img" aria-label="Street map of the office area"></div>
<svg class="abs map-pin" width="38" height="50" viewBox="0 0 38 50"><path d="M19 0 A19 19 0 0 1 38 19 C38 32 19 50 19 50 C19 50 0 32 0 19 A19 19 0 0 1 19 0Z" fill="#1b8dcc"/><circle cx="19" cy="19" r="8" fill="#fff"/></svg>
<div class="abs map-tag">MSIG</div>

<footer class="abs footer">
  <div class="col" style="left:111px">
    <h4>Links</h4>
    <ul><li>Customer Support</li><li>Services</li><li>Resources</li><li>FAQs</li><li>Contact Us</li></ul>
  </div>
  <div class="col" style="left:306px">
    <h4>Blog</h4>
    <div class="blog-item"><div class="thumb" role="img" aria-label="Blog thumbnail"></div><p>Tips for choosing the right policy for your growing family</p></div>
    <div class="blog-item"><div class="thumb" role="img" aria-label="Blog thumbnail"></div><p>What small business owners should know about liability coverage</p></div>
  </div>
  <div class="col contact-list" style="left:634px">
    <h4>Get in Touch</h4>
    <div style="margin-top:12px">
      <p>Address : 1180 Alder Crest Way, Suite<br>140 Harborview, FL 33000</p>
      <p>Phone : (555) 013-4410</p>
      <p>Email : info@meridianshield.example</p>
    </div>
  </div>
  <div class="col" style="left:885px">
    <h4>Newsletter</h4>
    <p class="news-note">Your latest news and updates will be sent here weekly.</p>
    <div class="news-form"><span>Email address</span><b>SUBMIT</b></div>
    <div class="rings"><span></span><span></span><span></span></div>
  </div>
</footer>
<div class="abs copyright">Copyright © 2016. All Rights Reserved</div>

</body>
</html>
```